Business card design needed

I would like a one sided black business card with the information provided above. Refer to my website www.brightvolleyracquets.com.au for an example of colors I have used for my site, would like to keep this consistent for my business cards also, I will upload my logo below.

I am a new small business that provides tennis customers with racquet re stringing, tennis strings and accessories.

Industry/Entity Type

Small Business

Contact Information for Business Card

Bright Volley Tennis

Owen Whitby
Managing Director

brightvolleyracquets@mailbox.example
www.brightvolleyracquets.com.au
0491 726 305

Racquet Restringing/Tennis Strings/Accessories

Requirements
Must have
• Must have my logo and card must be black

```html
<!DOCTYPE html>
<html lang="en">
<head>
<meta charset="utf-8">
<title>Bright Volley Tennis – Business Card</title>
<link rel="stylesheet" href="https://fonts.googleapis.com/css2?family=Source+Sans+3:wght@400;600;700&display=swap">
<style>
  :root {
    --stage: #e8e5e0;
    --card-black: #000000;
    --lime: #bfd843;
    --steel-blue: #3b6aa0;
    --white: #ffffff;
    --ink: #111111;
    --font-main: "Source Sans 3", "Myriad Pro", Arial, sans-serif;
  }
  * { margin: 0; padding: 0; box-sizing: border-box; }
  html, body {
    width: 1200px; height: 750px; overflow: hidden;
    background: var(--stage);
    font-family: var(--font-main);
  }
  .card {
    position: absolute; left: 75px; top: 75px;
    width: 1050px; height: 600px;
    background: var(--card-black);
    border-radius: 38px;
    overflow: hidden;
    box-shadow: 0 6px 18px rgba(0,0,0,0.25);
  }
  .card__bands { position: absolute; inset: 0; }
  .brand {
    position: absolute; left: 70px; top: 100px;
    display: flex; align-items: center; gap: 18px;
    color: var(--lime);
    font-weight: 700; font-size: 60px; letter-spacing: 0.5px;
  }
  .brand__dot {
    width: 46px; height: 46px; border-radius: 50%;
    background: var(--lime);
  }
  .services {
    position: absolute; left: 63px; top: 352px;
    list-style: none; color: var(--white);
    font-size: 34px; line-height: 45px;
  }
  .services li { display: flex; align-items: center; }
  .services li::before {
    content: ""; width: 9px; height: 9px; background: var(--white);
    margin-right: 14px;
  }
  .contact-person { position: absolute; left: 603px; top: 355px; }
  .contact-person__name {
    color: var(--lime); font-weight: 700; font-size: 34px; line-height: 40px;
  }
  .contact-person__role {
    color: var(--white); font-size: 25px; line-height: 32px; margin-top: 2px;
  }
  .contact-line {
    position: absolute; display: flex; align-items: center;
    font-size: 25px; gap: 14px; white-space: nowrap;
  }
  .contact-line svg { flex: none; }
  .contact-line--phone { left: 603px; top: 444px; color: var(--white); }
  .contact-line--email,
  .contact-line--web { font-size: 22px; gap: 12px; color: var(--ink); }
  .contact-line--email { left: 603px; top: 507px; }
  .contact-line--web { left: 603px; top: 542px; }
</style>
</head>
<body>
  <div class="card">
    <svg class="card__bands" width="1050" height="600" viewBox="0 0 1050 600" aria-hidden="true">
      <polygon points="0,547 520,547 490,580 0,580" fill="var(--steel-blue)"/>
      <polygon points="585,495 1050,495 1050,600 0,600 0,585 495,585" fill="var(--lime)"/>
    </svg>

    <div class="brand">
      <span class="brand__dot"></span>
      <span class="brand__name">Bright Volley Tennis</span>
    </div>

    <ul class="services">
      <li>Racquet Restringing</li>
      <li>Tennis Strings</li>
      <li>Accessories</li>
    </ul>

    <div class="contact-person">
      <p class="contact-person__name">Owen Whitby</p>
      <p class="contact-person__role">Managing Director</p>
    </div>

    <p class="contact-line contact-line--phone">
      <svg width="22" height="16" viewBox="0 0 22 16" aria-hidden="true">
        <path d="M1 6 Q11 -2 21 6 L18 8 L15 5 L7 5 L4 8 Z" fill="var(--lime)"/>
        <path d="M6 7 L16 7 L20 15 L2 15 Z" fill="var(--lime)"/>
        <circle cx="11" cy="11" r="2" fill="var(--card-black)"/>
      </svg>
      <span>0491 726 305</span>
    </p>
    <p class="contact-line contact-line--email">
      <svg width="22" height="16" viewBox="0 0 22 16" aria-hidden="true">
        <rect x="1" y="2" width="20" height="12" fill="none" stroke="var(--ink)" stroke-width="2"/>
        <path d="M1 2 L11 9 L21 2" fill="none" stroke="var(--ink)" stroke-width="2"/>
      </svg>
      <span>brightvolleyracquets@mailbox.example</span>
    </p>
    <p class="contact-line contact-line--web">
      <svg width="22" height="18" viewBox="0 0 18 18" aria-hidden="true">
        <circle cx="9" cy="9" r="8" fill="var(--ink)"/>
        <path d="M1 9 H17 M9 1 Q4 9 9 17 M9 1 Q14 9 9 17" fill="none" stroke="var(--lime)" stroke-width="1.2"/>
      </svg>
      <span>www.brightvolleyracquets.com.au</span>
    </p>
  </div>
</body>
</html>
```